Redesign of business card for Cedar Ridge Mechanical

We are looking for a new design for our business cards for Cedar Ridge Mechanical. We are a plumbing & HVAC construction company, operating on the West Coast of Canada and USA. Logo attached.
Industry/Entity Type
Construction - Plumbing & HVAC
Contact Information for Business Card
Name, address, phone numbers, email, website address
Look and feel
Each slider illustrates characteristics of the customer's brand and the style your logo design should communicate.

```html
<!DOCTYPE html>
<html lang="en">
<head>
<meta charset="UTF-8">
<title>Cedar Ridge Mechanical — Business Card</title>
<link href="https://fonts.googleapis.com/css2?family=Poppins:wght@400;500;600;700&display=swap" rel="stylesheet">
<style>
  :root {
    --backdrop: #222222;
    --card-light: #e0e0e0;
    --card-dark: #1f2023;
    --ink: #0d0d0d;
    --paper: #ffffff;
  }
  * { box-sizing: border-box; margin: 0; padding: 0; }
  html, body {
    width: 1200px; height: 780px; overflow: hidden;
    background: var(--backdrop);
    font-family: 'Poppins', sans-serif;
  }
  .canvas { position: relative; width: 1200px; height: 780px; }

  .card {
    position: absolute; top: 230px;
    width: 560px; height: 320px;
    border-radius: 18px; overflow: hidden;
  }
  .card--front { left: 20px; background: var(--card-light); color: var(--ink); }
  .card--back  { left: 620px; background: var(--card-dark); color: var(--paper); }

  /* Wordmark */
  .wordmark {
    display: flex; align-items: center; gap: 10px;
    font-weight: 600; text-transform: uppercase; letter-spacing: 0.5px;
  }
  .wordmark__square { flex: none; background: currentColor; }
  .card--front .wordmark {
    position: absolute; left: 30px; top: 70px; width: 220px;
    font-size: 17px; line-height: 1.25;
  }
  .card--front .wordmark__square { width: 16px; height: 16px; }
  .card--back .wordmark {
    position: absolute; left: 50%; top: 50%;
    transform: translate(-50%, -50%);
    font-size: 26px; white-space: nowrap;
  }
  .card--back .wordmark__square { width: 22px; height: 22px; }

  .divider {
    position: absolute; left: 268px; top: 42px;
    width: 1.5px; height: 220px; background: var(--ink);
  }

  .contact { position: absolute; left: 292px; top: 58px; }
  .contact__name { font-size: 33px; font-weight: 400; line-height: 1.05; letter-spacing: 0.3px; }
  .contact__name strong { font-weight: 700; }
  .contact__title { font-size: 14px; font-weight: 600; margin-top: 2px; }
  .contact__address { font-size: 14px; line-height: 1.35; margin-top: 8px; }
  .contact__list { list-style: none; margin-top: 8px; font-size: 14px; line-height: 1.5; }
  .contact__list li { display: flex; align-items: center; gap: 8px; }
  .contact__list svg { width: 12px; height: 12px; flex: none; }

  .band {
    position: absolute; bottom: 16px; height: 20px; background: var(--ink);
  }
  .band--left  { left: 0; width: 268px; clip-path: polygon(0 0, 100% 0, 94% 100%, 0 100%); }
  .band--right { left: 262px; right: 0; bottom: 0; height: 20px;
                 clip-path: polygon(6% 0, 100% 0, 100% 100%, 0 100%); left: 276px; }
</style>
</head>
<body>
<main class="canvas">

  <section class="card card--front" aria-label="Business card front">
    <div class="wordmark">
      <span class="wordmark__square"></span>
      <span class="wordmark__name">Cedar Ridge Mechanical</span>
    </div>

    <div class="divider"></div>

    <div class="contact">
      <h1 class="contact__name"><strong>Marta</strong> Novak</h1>
      <p class="contact__title">Founder &amp; CEO</p>
      <p class="contact__address">418 Harbor Lane Suite 120<br>Portland, OR 97204</p>
      <ul class="contact__list">
        <li>
          <svg viewBox="0 0 12 12" aria-hidden="true"><path d="M2.5 1h2l1 2.5-1.3 1a6 6 0 0 0 3.3 3.3l1-1.3L11 7.5v2A1.5 1.5 0 0 1 9.5 11 8.5 8.5 0 0 1 1 2.5 1.5 1.5 0 0 1 2.5 1z" fill="currentColor"/></svg>
          (503) 555-0147
        </li>
        <li>
          <svg viewBox="0 0 12 12" aria-hidden="true"><rect x="0.5" y="2" width="11" height="8" rx="1" fill="currentColor"/><path d="M1 2.8 6 6.5l5-3.7" stroke="#e0e0e0" stroke-width="1" fill="none"/></svg>
          info@cedarridgemech.com
        </li>
        <li>
          <svg viewBox="0 0 12 12" aria-hidden="true"><circle cx="6" cy="6" r="5.2" fill="currentColor"/><path d="M1 6h10M6 .8c-2.2 2.8-2.2 7.6 0 10.4M6 .8c2.2 2.8 2.2 7.6 0 10.4" stroke="#e0e0e0" stroke-width="0.8" fill="none"/></svg>
          www.cedarridgemech.com
        </li>
      </ul>
    </div>

    <div class="band band--left"></div>
    <div class="band band--right"></div>
  </section>

  <section class="card card--back" aria-label="Business card back">
    <div class="wordmark">
      <span class="wordmark__square"></span>
      <span class="wordmark__name">Cedar Ridge Mechanical</span>
    </div>
  </section>

</main>
</body>
</html>
```